Calm Harbor Bodywork business is seeking a Business Card Design

We are a new natural therapy business that needs a Business Card Design with an appointment card on the back.

We offer Myotherapy (muscle therapy) services and have a strong focus and commitment to helping people relieve pain and restore movement to their bodies.

I am attaching my business logo for you information.

Business card must contain my logo and have space for name, title, qualifications, phone number, email, web address

Appointment Card on the back of the card must contain space to write next appointment date, time and name of therapist and cancellation policy.

Cancellation Policy
Minimum of 24hrs notice is required prior to appointment time or full treatment fees with apply.

```html
<!DOCTYPE html>
<html lang="en">
<head>
<meta charset="utf-8">
<title>Calm Harbor Bodywork – Business Card</title>
<link rel="stylesheet" href="https://fonts.googleapis.com/css2?family=Quicksand:wght@400;500;700&display=swap">
<style>
  :root {
    --brand-red: #c01f30;
    --brand-green: #84bc3c;
    --paper: #ffffff;
    --ink-light: #ffffff;
  }
  * { box-sizing: border-box; margin: 0; padding: 0; }
  html, body { width: 1200px; height: 720px; overflow: hidden; background: var(--paper); }
  .card {
    position: relative;
    width: 1200px;
    height: 720px;
    background: var(--paper);
    font-family: "Quicksand", sans-serif;
    overflow: hidden;
  }
  .card__wave { position: absolute; inset: 0; width: 1200px; height: 720px; }
  .brand {
    position: absolute;
    left: 40px;
    top: 372px;
    width: 500px;
    text-align: center;
  }
  .brand__name {
    color: var(--brand-red);
    font-weight: 700;
    font-size: 42px;
    letter-spacing: 1px;
    line-height: 1.1;
    white-space: nowrap;
  }
  .identity {
    position: absolute;
    left: 660px;
    top: 52px;
    width: 420px;
    text-align: center;
    font-weight: 700;
  }
  .identity__name { color: var(--brand-red); font-size: 44px; letter-spacing: 2px; line-height: 1.15; }
  .identity__title { color: var(--ink-light); font-size: 35px; letter-spacing: 1.5px; line-height: 1.2; margin-top: 2px; }
  .identity__qual { color: var(--ink-light); font-size: 25px; letter-spacing: 1.5px; margin-top: 8px; }
  .contacts { position: absolute; left: 581px; top: 209px; list-style: none; }
  .contact {
    display: flex;
    align-items: center;
    height: 81px;
    margin-bottom: 27px;
  }
  .contact__icon {
    flex: none;
    width: 81px;
    height: 81px;
    background: var(--paper);
    border: 4px solid var(--brand-red);
    border-radius: 4px;
    padding: 5px;
  }
  .contact__icon svg { display: block; width: 100%; height: 100%; }
  .contact__text {
    margin-left: 17px;
    color: var(--ink-light);
    font-size: 29px;
    font-weight: 500;
    letter-spacing: 2.2px;
    line-height: 1.2;
    white-space: nowrap;
  }
</style>
</head>
<body>
<main class="card">
  <svg class="card__wave" viewBox="0 0 1200 720" aria-hidden="true">
    <path d="M538 0 C 596 200, 626 460, 552 720 L1200 720 L1200 0 Z" fill="var(--brand-red)"/>
    <path d="M560 0 C 616 200, 644 460, 574 720 L1200 720 L1200 0 Z" fill="var(--brand-green)"/>
  </svg>

  <section class="brand">
    <p class="brand__name">Calm Harbor Bodywork</p>
  </section>

  <header class="identity">
    <h1 class="identity__name">Helen Marsh</h1>
    <p class="identity__title">Myotherapist</p>
    <p class="identity__qual">Adv. Dip. Myotherapy</p>
  </header>

  <ul class="contacts">
    <li class="contact">
      <span class="contact__icon">
        <svg viewBox="0 0 60 60" aria-hidden="true">
          <rect width="60" height="60" fill="var(--brand-red)"/>
          <path d="M10 22 Q30 8 50 22 L46 28 L39 25 L38 20 Q30 17 22 20 L21 25 L14 28 Z" fill="#fff"/>
          <path d="M18 30 L22 24 L38 24 L42 30 L46 48 L14 48 Z" fill="#fff"/>
          <g fill="var(--brand-red)">
            <rect x="23" y="32" width="3" height="3"/><rect x="28.5" y="32" width="3" height="3"/><rect x="34" y="32" width="3" height="3"/>
            <rect x="23" y="37" width="3" height="3"/><rect x="28.5" y="37" width="3" height="3"/><rect x="34" y="37" width="3" height="3"/>
            <rect x="23" y="42" width="3" height="3"/><rect x="28.5" y="42" width="3" height="3"/><rect x="34" y="42" width="3" height="3"/>
          </g>
        </svg>
      </span>
      <span class="contact__text">+61 3 9000 4172</span>
    </li>
    <li class="contact">
      <span class="contact__icon">
        <svg viewBox="0 0 60 60" aria-hidden="true">
          <rect width="60" height="60" fill="var(--brand-red)"/>
          <rect x="9" y="16" width="42" height="28" fill="none" stroke="#fff" stroke-width="2.5"/>
          <path d="M9 16 L30 33 L51 16 M9 44 L24 29 M51 44 L36 29" fill="none" stroke="#fff" stroke-width="2.5"/>
        </svg>
      </span>
      <span class="contact__text">info@calmharborbody.com.au</span>
    </li>
    <li class="contact">
      <span class="contact__icon">
        <svg viewBox="0 0 60 60" aria-hidden="true">
          <rect width="60" height="60" fill="var(--brand-red)"/>
          <circle cx="30" cy="30" r="19" fill="#fff"/>
          <circle cx="30" cy="30" r="14" fill="var(--brand-red)"/>
          <path d="M22 22 Q30 18 33 24 Q28 30 34 34 Q30 42 26 40 Q24 32 20 30 Z" fill="#fff"/>
        </svg>
      </span>
      <span class="contact__text">www.calmharborbody.com.au</span>
    </li>
    <li class="contact">
      <span class="contact__icon">
        <svg viewBox="0 0 60 60" aria-hidden="true">
          <rect width="60" height="60" fill="#fff"/>
          <path d="M30 8 L56 32 L50 32 L30 14 L10 32 L4 32 Z" fill="var(--brand-red)"/>
          <path d="M12 30 L30 14 L48 30 L48 54 L35 54 L35 40 L25 40 L25 54 L12 54 Z" fill="var(--brand-red)"/>
        </svg>
      </span>
      <span class="contact__text">Level 1/58 Tidewater Rd,<br>Alderly VIC 3081</span>
    </li>
  </ul>
</main>
</body>
</html>
```